Web Site Design and Business Card design for Recruiting Company

There are three major tasks in this project:
1) I need to re-design my newly created website www.talvoro.net using the same logo but creating a totally different recruiting template that will apply better for a recruitment site. I want to use the elements of the Talvoro Network logo (which is the road junction) and red, black and gray colors throughout the website. I need someone to both design and launch the site...
2) I would also like to design a double sided business card using the same logo/colors and elements as described above
3) I would also like to have a small thumbnail logo created. As our large logo cannot be previewed easily on the Pelmwork or on Google Chrome tab images

The design should be contemporary, minimalist and slick

```html
<!DOCTYPE html>
<html lang="en">
<head>
<meta charset="utf-8">
<title>Talvoro Network – Recruiting</title>
<link href="https://fonts.googleapis.com/css2?family=Roboto:wght@400;500;700&family=Open+Sans:wght@400;600&display=swap" rel="stylesheet">
<style>
:root{
  --red:#e52434;
  --red-dark:#d61f2e;
  --red-soft:#ff6b78;
  --ink:#222;
  --text:#555;
  --gray-bg:#f1f1f1;
  --line:#d9d9d9;
  --black:#0c0c0c;
  --white:#fff;
}
*{margin:0;padding:0;box-sizing:border-box}
html,body{width:1200px;height:4367px;overflow:hidden}
body{font-family:"Open Sans",sans-serif;color:var(--text);background:var(--white);position:relative}
.section{position:absolute;left:0;width:1200px}
.abs{position:absolute}
.h-title{font-family:"Roboto",sans-serif;font-weight:700;color:var(--red);text-align:center;font-size:38px;letter-spacing:.3px}
.center{left:0;width:1200px;text-align:center}

/* top bar */
.topbar{top:0;height:46px;background:#f5f5f5;font-size:17px;color:var(--ink)}
.topbar .item{top:11px;display:flex;align-items:center;gap:14px}
.topbar .social{right:88px;top:12px;display:flex;gap:9px}
.dot{width:21px;height:21px;border-radius:50%;background:#3a5ba0}

/* header */
.header{top:46px;height:112px;background:var(--white)}
.brand{left:88px;top:10px;width:132px;height:92px;display:flex;align-items:center;justify-content:center;font-family:"Roboto",sans-serif;font-weight:500;font-size:17px;color:var(--ink);text-align:center;line-height:1.3}
.nav{top:44px;font-size:16px;color:var(--ink)}
.nav.active{color:var(--red)}
.nav.active::after{content:"";position:absolute;left:0;right:0;bottom:-4px;height:2px;background:var(--red)}

/* hero */
.hero{top:158px;height:613px;background:linear-gradient(110deg,#3b3430 0%,#6b625b 35%,#c8c2bb 60%,#8a817a 100%)}
.hero h1{top:244px;font-family:"Roboto",sans-serif;font-weight:500;font-size:31px;color:var(--white)}
.hero .sub{top:290px;font-family:"Roboto",sans-serif;font-weight:500;font-size:17px;color:var(--white)}
.search{left:125px;top:332px;width:912px;height:100px;background:rgba(229,36,52,.78);border-radius:6px}
.field{top:32px;height:42px;background:var(--white);border-radius:4px;font-size:14px;color:#777;padding:0 12px;display:flex;align-items:center;justify-content:space-between}
.btn-search{left:770px;top:32px;width:132px;height:42px;border:2px solid var(--white);background:var(--red);border-radius:4px;color:var(--white);font-family:"Roboto",sans-serif;font-weight:500;font-size:16px;display:flex;align-items:center;justify-content:center}

/* steps */
.steps{top:771px;height:237px;background:var(--red)}
.steps .bar{left:270px;top:81px;width:640px;height:10px;background:#ff7480}
.step{width:124px;height:124px;border-radius:50%;background:var(--white);border:6px solid #ff7480;top:24px;display:flex;align-items:center;justify-content:center}
.step-label{top:152px;width:260px;text-align:center;color:var(--white);font-size:17px;line-height:27px}

/* welcome */
.welcome{top:1008px;height:404px}
.welcome h2{left:88px;top:58px;font-family:"Roboto",sans-serif;font-weight:700;font-size:37px;color:var(--red)}
.welcome p{left:88px;top:122px;width:468px;font-size:16px;line-height:27px;text-align:justify}
.btn{background:var(--red);color:var(--white);font-family:"Roboto",sans-serif;font-weight:500;display:flex;align-items:center;justify-content:center;border-radius:4px}
.welcome .btn{left:90px;top:282px;width:176px;height:56px;font-size:20px}
.photo-card{top:65px;width:244px;height:275px;border-radius:4px;overflow:hidden}
.photo-card .ph{height:228px}
.photo-card .cap{height:47px;background:var(--red);color:var(--white);font-family:"Roboto",sans-serif;font-weight:500;font-size:14px;padding:0 12px;display:flex;align-items:center;justify-content:space-between}

/* jobs */
.jobs{top:1412px;height:695px;background:var(--gray-bg)}
.jobs .h-title{top:48px}
.jobs .lead{top:103px;font-size:17px}
.job{left:210px;width:782px;height:112px;background:var(--white);border:1px solid var(--line);box-shadow:0 2px 6px rgba(0,0,0,.15)}
.job .t{left:47px;top:22px;font-family:"Roboto",sans-serif;font-weight:500;font-size:21px;color:var(--red)}
.job .m{left:47px;font-size:14px;color:var(--ink);display:flex;align-items:center;gap:8px}
.job .pay{left:456px;top:28px;font-family:"Roboto",sans-serif;font-size:16px;color:var(--red);font-weight:500}
.job .type{left:456px;top:56px;font-size:14px;color:#1b7b3a}
.job .btn{left:599px;top:32px;width:142px;height:40px;font-size:14px}
.jobs .all{left:514px;top:581px;width:176px;height:58px;font-size:20px}

/* services */
.services{top:2107px;height:617px}
.services .h-title{top:56px}
.services .lead{top:114px;font-size:21px;line-height:38px}
.svc{top:246px;width:238px;height:283px;background:var(--white);box-shadow:0 2px 10px rgba(0,0,0,.16);text-align:center}
.svc h3{font-family:"Roboto",sans-serif;font-weight:500;font-size:21px;color:var(--red);line-height:27px;position:absolute;left:0;right:0}
.svc p{position:absolute;left:14px;right:14px;top:160px;font-size:13px;line-height:21px;color:var(--ink)}
.svc .icon{position:absolute;left:84px;top:16px}
.svc .go{position:absolute;left:96px;bottom:-23px;width:46px;height:46px;border-radius:50%;background:var(--red);display:flex;align-items:center;justify-content:center}

/* blog */
.blog{top:2724px;height:619px;background:linear-gradient(180deg,#ff6875 0%,#e8283a 100%)}
.blog .h-title{top:36px;color:var(--white)}
.post{top:119px;width:327px}
.post .ph{height:272px}
.post .av{position:absolute;left:230px;top:235px;width:74px;height:74px;border-radius:50%;border:3px solid var(--white);background:linear-gradient(135deg,#d9b9a0,#8b6a55)}
.post .date{position:absolute;top:282px;left:0;font-size:14px;color:var(--white);display:flex;gap:8px;align-items:center}
.post h4{position:absolute;top:318px;left:0;font-family:"Roboto",sans-serif;font-weight:700;font-size:22px;color:var(--white)}
.post p{position:absolute;top:361px;left:0;width:310px;font-size:14px;line-height:27px;color:var(--white);text-align:justify}

/* testimonial */
.quote{top:3343px;height:607px}
.quote .h-title{top:64px}
.quote .txt{top:215px;left:135px;width:930px;text-align:center;font-size:19px;line-height:36px;color:#666}
.quote .face{left:538px;top:382px;width:122px;height:122px;border-radius:50%;border:3px solid var(--ink);background:linear-gradient(135deg,#e6d3c4,#9c8170)}
.quote .name{top:527px;font-family:"Roboto",sans-serif;font-weight:500;font-size:23px;color:var(--red)}

/* footer */
.footer{top:3950px;height:344px;background:var(--black);color:var(--white)}
.footer h5{top:70px;font-family:"Roboto",sans-serif;font-weight:500;font-size:27px}
.footer .col{top:122px;font-size:15px;line-height:27px}
.footer .email{left:90px;top:226px;width:239px;height:40px;background:var(--white);border-radius:4px;color:#333;font-size:13px;padding:0 12px;display:flex;align-items:center}
.footer .send{left:90px;top:290px;width:129px;height:42px;font-size:17px}
.legal{top:4294px;height:73px;background:var(--black);border-top:1px solid #333;color:var(--white);font-size:15px}
</style>
</head>
<body>

<div class="section topbar">
  <div class="abs item" style="left:105px">
    <svg width="18" height="18" viewBox="0 0 24 24"><rect width="24" height="24" rx="4" fill="#e52434"/><path d="M8 6c1 3 3 6 10 11l-2 2C9 15 6 11 5 8z" fill="#fff"/></svg>
    +1-555-013-0636
  </div>
  <div class="abs item" style="left:338px;font-size:15px">
    <svg width="18" height="16" viewBox="0 0 24 20"><rect width="24" height="20" rx="3" fill="#e52434"/><path d="M4 5l8 6 8-6" stroke="#fff" stroke-width="2" fill="none"/></svg>
    info@talvoro.net
  </div>
  <div class="abs social">
    <span class="dot"></span><span class="dot" style="background:#2c6fb0"></span><span class="dot" style="background:#3fa8e8"></span><span class="dot" style="background:#e01c1c"></span><span class="dot" style="background:#c0368c"></span>
  </div>
</div>

<header class="section header">
  <div class="abs brand">Talvoro<br>Network</div>
  <a class="abs nav active" style="left:673px">Home</a>
  <a class="abs nav" style="left:776px">About Us</a>
  <a class="abs nav" style="left:903px">Services</a>
  <a class="abs nav" style="left:1027px">Contact Us</a>
</header>

<section class="section hero" role="img" aria-label="Photo of two business people shaking hands across a desk">
  <h1 class="abs center">JOIN US &amp; EXPLORE THOUSANDS OF JOBS</h1>
  <p class="abs center sub">Select your industry and/or type your keyword, then click search to find your perfect job</p>
  <div class="abs search">
    <div class="abs field" style="left:20px;width:254px">Job search <svg width="14" height="9"><path d="M1 1l6 6 6-6" stroke="#333" stroke-width="2" fill="none"/></svg></div>
    <div class="abs field" style="left:288px;width:254px">Location <svg width="14" height="9"><path d="M1 1l6 6 6-6" stroke="#333" stroke-width="2" fill="none"/></svg></div>
    <div class="abs field" style="left:560px;width:200px">Specialism</div>
    <div class="abs btn-search">Search</div>
  </div>
</section>

<section class="section steps">
  <div class="abs bar"></div>
  <div class="abs step" style="left:208px"><svg width="60" height="60" viewBox="0 0 60 60"><circle cx="30" cy="30" r="28" fill="#111"/><circle cx="30" cy="23" r="8" fill="#fff"/><path d="M16 44c3-8 25-8 28 0" fill="#fff"/></svg></div>
  <div class="abs step" style="left:528px"><svg width="64" height="60" viewBox="0 0 64 60"><path d="M32 40V6M20 18l12-12 12 12" stroke="#111" stroke-width="4" fill="none"/><path d="M6 34v20h52V34" stroke="#111" stroke-width="4" fill="none"/></svg></div>
  <div class="abs step" style="left:848px"><svg width="60" height="64" viewBox="0 0 60 64"><rect x="6" y="4" width="38" height="50" rx="2" stroke="#111" stroke-width="3" fill="none"/><circle cx="24" cy="18" r="5" fill="#111"/><path d="M14 34h20M14 42h14" stroke="#111" stroke-width="3"/><circle cx="42" cy="44" r="9" stroke="#111" stroke-width="3" fill="#fff"/><path d="M48 51l8 8" stroke="#111" stroke-width="4"/></svg></div>
  <p class="abs step-label" style="left:140px">1. Register account<br>to begin applying</p>
  <p class="abs step-label" style="left:460px">2. Upload your Resume<br>&amp; browse hundreds of jobs</p>
  <p class="abs step-label" style="left:780px;top:156px">3. Apply for jobs<br>in seconds</p>
</section>

<section class="section welcome">
  <h2 class="abs">Welcome to Talvoro</h2>
  <p class="abs">Talvoro Network LLC is an Atlanta based talent advisory, recruiting and staffing firm. We help companies find skilled professionals within the shortest time frames though our unique network of business and personal connections nationwide and overseas.</p>
  <a class="abs btn">READ MORE</a>
  <div class="abs photo-card" style="left:600px">
    <div class="ph" role="img" aria-label="Photo of a smiling businessman in a suit" style="background:linear-gradient(160deg,#c9ccd2,#5a5e66)"></div>
    <div class="cap">Create your profile <svg width="10" height="14"><path d="M2 2l5 5-5 5" stroke="#fff" stroke-width="2" fill="none"/></svg></div>
  </div>
  <div class="abs photo-card" style="left:866px">
    <div class="ph" role="img" aria-label="Photo of a resume on a clipboard with a pen" style="background:linear-gradient(160deg,#e9edf2,#a8b4c2)"></div>
    <div class="cap">Upload your CV <svg width="10" height="14"><path d="M2 2l5 5-5 5" stroke="#fff" stroke-width="2" fill="none"/></svg></div>
  </div>
</section>

<section class="section jobs">
  <h2 class="abs h-title center">RECENT JOBS</h2>
  <p class="abs center lead">Know your worth and find the job that qualify your life</p>

  <div class="abs job" style="top:163px">
    <div class="abs t">INFORMATION TECHNOLOGY (IT)</div>
    <div class="abs m" style="top:54px"><svg width="14" height="14"><circle cx="7" cy="7" r="7" fill="#e52434"/></svg>GERMANY , HANOVER</div>
    <div class="abs m" style="top:79px"><svg width="14" height="14"><rect x="2" y="6" width="10" height="8" fill="#e52434"/><path d="M4 6V4a3 3 0 016 0v2" stroke="#e52434" stroke-width="2" fill="none"/></svg>Expired</div>
    <div class="abs pay">$ 31000</div><div class="abs type">FULL TIME</div>
    <a class="abs btn">VIEW MORE</a>
  </div>
  <div class="abs job" style="top:293px">
    <div class="abs t">TELECOMMUNICATIONS</div>
    <div class="abs m" style="top:54px"><svg width="14" height="14"><circle cx="7" cy="7" r="7" fill="#e52434"/></svg>GERMANY , HANOVER</div>
    <div class="abs m" style="top:79px"><svg width="14" height="14"><rect x="2" y="6" width="10" height="8" fill="#e52434"/><path d="M4 6V4a3 3 0 016 0v2" stroke="#e52434" stroke-width="2" fill="none"/></svg>Expired</div>
    <div class="abs pay">$ 31000</div><div class="abs type">FULL TIME</div>
    <a class="abs btn">VIEW MORE</a>
  </div>
  <div class="abs job" style="top:425px;left:208px">
    <div class="abs t">ACCOUNTING &amp; FINANCE</div>
    <div class="abs m" style="top:54px"><svg width="14" height="14"><circle cx="7" cy="7" r="7" fill="#e52434"/></svg>GERMANY , HANOVER</div>
    <div class="abs m" style="top:79px"><svg width="14" height="14"><rect x="2" y="6" width="10" height="8" fill="#e52434"/><path d="M4 6V4a3 3 0 016 0v2" stroke="#e52434" stroke-width="2" fill="none"/></svg>Expired</div>
    <div class="abs pay">$ 31000</div><div class="abs type">FULL TIME</div>
    <a class="abs btn">VIEW MORE</a>
  </div>
  <a class="abs btn all">ALL JOBS</a>
</section>

<section class="section services">
  <h2 class="abs h-title center">SERVICES</h2>
  <p class="abs center lead">We specialize in sourcing, recruiting, placement and staffing of candidates<br>in the following categories:</p>

  <div class="abs svc" style="left:130px">
    <svg class="icon" width="70" height="64" viewBox="0 0 70 64"><rect x="6" y="12" width="58" height="40" rx="3" stroke="#e52434" stroke-width="3" fill="none"/><path d="M14 44l12-14 10 8 14-16" stroke="#e52434" stroke-width="3" fill="none"/><path d="M2 56h66" stroke="#e52434" stroke-width="3"/></svg>
    <h3 style="top:98px">Information<br>Technology (IT)</h3>
    <p>Lorem ipsum dolor sit amet, consectetur adipiscing elit, sed do eiusmod tempor incididunt ut labore et dolore magna aliqua</p>
    <span class="go"><svg width="12" height="14"><path d="M3 2l5 5-5 5" stroke="#fff" stroke-width="2" fill="none"/></svg></span>
  </div>
  <div class="abs svc" style="left:466px">
    <svg class="icon" width="70" height="64" viewBox="0 0 70 64"><rect x="4" y="20" width="26" height="22" stroke="#e52434" stroke-width="3" fill="none"/><rect x="40" y="20" width="26" height="22" stroke="#e52434" stroke-width="3" fill="none"/><path d="M26 8h18M40 4l4 4-4 4M8 58c2-10 18-10 20 0M42 58c2-10 18-10 20 0" stroke="#e52434" stroke-width="3" fill="none"/></svg>
    <h3 style="top:104px">Telecommunications</h3>
    <p style="top:150px">Lorem ipsum dolor sit amet, consectetur adipiscing elit, sed do eiusmod tempor incididunt ut labore et dolore magna aliqua</p>
    <span class="go"><svg width="12" height="14"><path d="M3 2l5 5-5 5" stroke="#fff" stroke-width="2" fill="none"/></svg></span>
  </div>
  <div class="abs svc" style="left:800px">
    <svg class="icon" width="70" height="64" viewBox="0 0 70 64"><rect x="8" y="4" width="34" height="54" rx="3" stroke="#e52434" stroke-width="3" fill="none"/><path d="M14 12h22M14 22h6M24 22h6M14 30h6M24 30h6" stroke="#e52434" stroke-width="3"/><circle cx="28" cy="46" r="8" stroke="#e52434" stroke-width="3" fill="#fff"/><path d="M50 14l12 12-18 22-10 2 2-10z" stroke="#e52434" stroke-width="3" fill="none"/></svg>
    <h3 style="top:98px">Accounting &amp;<br>Finance</h3>
    <p>Lorem ipsum dolor sit amet, consectetur adipiscing elit, sed do eiusmod tempor incididunt ut labore et dolore magna aliqua</p>
    <span class="go"><svg width="12" height="14"><path d="M3 2l5 5-5 5" stroke="#fff" stroke-width="2" fill="none"/></svg></span>
  </div>
</section>

<section class="section blog">
  <h2 class="abs h-title center">OUR BLOG</h2>
  <article class="abs post" style="left:88px">
    <div class="ph" role="img" aria-label="Photo of colleagues reviewing documents at an office table" style="background:linear-gradient(135deg,#eef0f2,#8d939b)"></div>
    <div class="av" role="img" aria-label="Author portrait"></div>
    <div class="date"><svg width="14" height="14"><rect x="1" y="2" width="12" height="11" fill="none" stroke="#fff" stroke-width="1.5"/><path d="M1 6h12" stroke="#fff"/></svg>OCTOBER 19, 2016</div>
    <h4>LOREM IPSUM DOLOR SIT</h4>
    <p>Lorem ipsum dolor sit amet, consectetur adipiscing elit. Fusce risus leo, imperdiet in metus vel, luctus aliquet felis. Quisque eget congue.</p>
  </article>
  <article class="abs post" style="left:436px">
    <div class="ph" role="img" aria-label="Photo of a meeting seen from above around a white table" style="background:linear-gradient(135deg,#6e6258,#ded9d2)"></div>
    <div class="av" role="img" aria-label="Author portrait"></div>
    <div class="date"><svg width="14" height="14"><rect x="1" y="2" width="12" height="11" fill="none" stroke="#fff" stroke-width="1.5"/><path d="M1 6h12" stroke="#fff"/></svg>OCTOBER 19, 2016</div>
    <h4>LOREM IPSUM DOLOR SIT</h4>
    <p>Lorem ipsum dolor sit amet, consectetur adipiscing elit. Fusce risus leo, imperdiet in metus vel, luctus aliquet felis. Quisque eget turpis ac congue.</p>
  </article>
  <article class="abs post" style="left:783px">
    <div class="ph" role="img" aria-label="Photo of a job interview in a bright office" style="background:linear-gradient(135deg,#f2f2f0,#4e5a6e)"></div>
    <div class="av" role="img" aria-label="Author portrait"></div>
    <div class="date"><svg width="14" height="14"><rect x="1" y="2" width="12" height="11" fill="none" stroke="#fff" stroke-width="1.5"/><path d="M1 6h12" stroke="#fff"/></svg>OCTOBER 19, 2016</div>
    <h4>LOREM IPSUM DOLOR SIT</h4>
    <p>Lorem ipsum dolor sit amet, consectetur adipiscing elit. Fusce risus leo, imperdiet in metus vel, luctus aliquet felis. Quisque ac ipsum laoreet congue.</p>
  </article>
</section>

<section class="section quote">
  <h2 class="abs h-title center">WHAT OUR USERS SAY</h2>
  <svg class="abs" style="left:580px;top:156px" width="40" height="34" viewBox="0 0 40 34"><path d="M0 34V18C0 8 5 2 15 0v6c-5 2-7 5-7 10h7v18zM22 34V18C22 8 27 2 37 0v6c-5 2-7 5-7 10h7v18z" fill="#555"/></svg>
  <svg class="abs" style="left:88px;top:255px" width="16" height="26"><path d="M13 2L3 13l10 11" stroke="#333" stroke-width="2.5" fill="none"/></svg>
  <svg class="abs" style="left:1095px;top:255px" width="16" height="26"><path d="M3 2l10 11L3 24" stroke="#333" stroke-width="2.5" fill="none"/></svg>
  <p class="abs txt">Lorem ipsum dolor sit amet, consectetur adipiscing elit, sed do eiusmod tempor incididunt ut labore et dolore magna aliqua. Ut enim ad minim veniam, quis nostrud exercitation ullamco laboris nisi ut aliquip ex ea commodo consequat. Duis aute irure dolor in reprehenderit in voluptate velit esse cillum dolore eu fugiat nulla pariatur</p>
  <div class="abs face" role="img" aria-label="Portrait of the reviewer"></div>
  <p class="abs center name">DANA WHITLOW</p>
</section>

<footer class="section footer">
  <h5 class="abs" style="left:88px">Newsletter</h5>
  <p class="abs col" style="left:90px;width:280px;font-size:14px">Sed consequat sapien faucibus quam bibendum convallis quis in nulla. Pellentesque volutpat odio eget diam</p>
  <div class="abs email">Enter the Email</div>
  <a class="abs btn send">Send</a>

  <h5 class="abs" style="left:441px">Other</h5>
  <p class="abs col" style="left:441px;top:128px">Home<br>About Us<br>Services<br>Contact Us</p>

  <h5 class="abs" style="left:639px">Candidates</h5>
  <p class="abs col" style="left:641px;top:124px">Browse Jobs<br>Browse<br>Categories<br>Candidate Profile<br>Edit Resume<br>Saved Jobs</p>

  <h5 class="abs" style="left:883px">Contact us</h5>
  <p class="abs col" style="left:883px;top:126px">1-555-013-0636<br>info@talvoro.net<br>hr@talvoro.net<br>Mon - Thu : 10.00Am - 6.00Pm<br>Fri:&nbsp;&nbsp;&nbsp;&nbsp;&nbsp;&nbsp;10:00 AM – 4:00 PM<br>Sat:&nbsp;&nbsp;&nbsp;&nbsp;&nbsp;12:00 PM – 2:00 PM<br>(by appointment only)</p>
</footer>

<div class="section legal">
  <p class="abs" style="left:90px;top:26px">© 2019 talvoro. All Rights Reserved</p>
  <div class="abs" style="left:958px;top:26px;display:flex;gap:10px">
    <span class="dot" style="background:#fff"></span><span class="dot" style="background:#fff"></span><span class="dot" style="background:#fff"></span><span class="dot" style="background:#fff"></span><span class="dot" style="background:#fff"></span>
  </div>
</div>

</body>
</html>
```